Private practice for psychiatry and psychotherapy needs a business card and logo

I need a logo and business card design for my private practice for psychiatry and psychotherapy. The optional names for my practice are: Vorsteling Praktijk voor Psychiatrie en Psychotherapie, or short: Praktijk Vorsteling.
I am a (child and adolescent) psychiatrist and psychotherapist. I diagnose and treat infants, children, adolescents and adults with psychiatric symptoms/disorders. I also give supervision to colleagues about their own treatments. My work is characterised by personal involvement, transparence, creativity and professionality.
I would like to have an appealing, light and bright, yet basic design that invites people (both children and adults) to contact me, gives trust and hope, without loosing professional appearance.
I uploaded my contact information which should not necessarily be all included (in this form) on the card as long as people know how to contact me. Please feel free to be creative!
Please note that my website is only temporarely and need a new design and update too!

Target Market(s)

Clients and patients (children, adolescents, adults) with psychiatric symptoms who need diagnosis and treatment. I work with private clients and patients through medical insurances.

Industry/Entity Type

Mental Health

Contact Information for Business Card

Dr. Ilse Vorsteling-ter Haaf
Psychiater/Kinder- en Jeugdpsychiater
Jorisvan Heultstraat 14
3071 PW Rotterdam
t: 06-58190274
e: info@praktijkvorsteling.nl
i: www.praktijkvorsteling.nl

Logo Text

Praktijk Vorsteling voor Psychiatrie en Psychotherapie; or short: Praktijk Vorsteling

Font styles to use
Sans Serif
Other font styles liked:
• up to designer

Requirements
Must have
• Appealing, light, bright, creative, trustful, professional and unique.

```html
<!DOCTYPE html>
<html lang="nl">
<head>
<meta charset="utf-8">
<title>Praktijk Vorsteling – visitekaartje</title>
<link rel="stylesheet" href="https://fonts.googleapis.com/css2?family=Exo+2:wght@400;600;700&display=swap">
<style>
  :root {
    --bg-top: #6b6b6b;
    --bg-bottom: #444444;
    --card-white: #ffffff;
    --card-orange: #b95c17;
    --brand-green: #5a9e16;
    --brand-orange: #f07d00;
    --text-grey: #555555;
    --logo-grey: #6f6f6f;
  }
  * { margin: 0; padding: 0; box-sizing: border-box; }
  html, body {
    width: 1200px; height: 900px; overflow: hidden;
  }
  body {
    position: relative;
    background: linear-gradient(180deg, var(--bg-top) 0%, var(--bg-bottom) 100%);
    font-family: "Exo 2", "Trebuchet MS", sans-serif;
  }
  .card {
    position: absolute;
    top: 184px;
    height: 491px;
    border-radius: 14px;
    box-shadow: 0 2px 6px rgba(0,0,0,0.18);
  }
  .card--front { left: 299px; width: 301px; background: var(--card-white); }
  .card--back {
    left: 645px; width: 305px;
    background: radial-gradient(circle at 50% 45%, #c0651f 0%, var(--card-orange) 70%);
  }

  .brand {
    position: absolute; left: 0; right: 0;
    display: flex; flex-direction: column; align-items: center;
    text-align: center;
    font-weight: 700;
  }
  .brand__dot {
    width: 62px; height: 62px; border-radius: 50%;
    margin-bottom: 16px;
  }
  .brand__name { font-size: 14.5px; line-height: 16px; letter-spacing: 0.1px; }
  .brand__name span { display: block; font-size: 12px; line-height: 15px; }

  .card--front .brand { top: 77px; color: var(--brand-green); }
  .card--front .brand__dot { background: var(--brand-green); }
  .card--back .brand { top: 195px; color: #ffffff; }
  .card--back .brand__dot { background: #ffffff; width: 60px; height: 60px; margin-bottom: 13px; }

  .person { position: absolute; left: 36px; top: 246px; }
  .person__name {
    font-size: 17px; line-height: 20px; font-weight: 700;
    text-transform: uppercase; letter-spacing: 0.2px;
  }
  .person__name .first { display: block; color: var(--brand-orange); }
  .person__name .second { display: block; color: var(--brand-green); }
  .person__role { margin-top: 9px; font-size: 14px; color: var(--text-grey); }

  .contact { position: absolute; left: 36px; top: 330px; list-style: none; }
  .contact li {
    display: flex; align-items: center; gap: 9px;
    height: 22px; font-size: 14px; color: var(--text-grey);
  }
  .contact svg { width: 15px; height: 15px; flex: none; }

  .address {
    position: absolute; left: 36px; top: 409px;
    font-style: normal; font-size: 14px; line-height: 18px; color: var(--text-grey);
  }
</style>
</head>
<body>
  <section class="card card--front" aria-label="Voorzijde visitekaartje">
    <div class="brand">
      <div class="brand__dot"></div>
      <p class="brand__name">PRAKTIJK VOOR PSYCHIATRIE EN<span>Psychotherapie Vorsteling</span></p>
    </div>

    <div class="person">
      <h1 class="person__name"><span class="first">Dr. Ilse Vorsteling-</span><span class="second">ter Haaf</span></h1>
      <p class="person__role">Psychiater/kinder- en jeugdpsychiater</p>
    </div>

    <ul class="contact">
      <li>
        <svg viewBox="0 0 16 16" aria-hidden="true"><circle cx="8" cy="8" r="8" fill="#f07d00"/><path d="M4.5 6.5c0-1 1.5-2 3.5-2s3.5 1 3.5 2l-1.2.3-.4-1.1H6.1l-.4 1.1zM5.5 7.5h5l.8 3.5H4.7z" fill="#fff"/></svg>
        06-58190274
      </li>
      <li>
        <svg viewBox="0 0 16 16" aria-hidden="true"><circle cx="8" cy="8" r="8" fill="#f07d00"/><rect x="4.3" y="5.3" width="7.4" height="5.4" fill="#fff"/><path d="M4.3 5.3 8 8.3l3.7-3" fill="none" stroke="#f07d00" stroke-width="0.9"/></svg>
        info@praktijkvorsteling.nl
      </li>
      <li>
        <svg viewBox="0 0 16 16" aria-hidden="true"><circle cx="8" cy="8" r="8" fill="#f07d00"/><circle cx="8" cy="8" r="3.8" fill="none" stroke="#fff" stroke-width="1.3"/><path d="M4.2 8h7.6M8 4.2v7.6" stroke="#fff" stroke-width="1"/></svg>
        www.praktijkvorsteling.nl
      </li>
    </ul>

    <address class="address">Jorisvan Heultstraat 14<br>3071 PW Rotterdam</address>
  </section>

  <section class="card card--back" aria-label="Achterzijde visitekaartje">
    <div class="brand">
      <div class="brand__dot"></div>
      <p class="brand__name">PRAKTIJK VOOR PSYCHIATRIE EN<span>Psychotherapie Vorsteling</span></p>
    </div>
  </section>
</body>
</html>
```